Simple, High-Class Web Design Wanted - Motivational Speakers Site

1. Full Brief/Request & Specs outlined on following video -
http://clipvault-demo.com/watch/rTkWmaPzQb

2. Use colours, images as you feel suits objective (we are happy to pay up to US$30 for any good images but must have licence/permission).

3. Layout probably similar to existing site - www.podiumtalentgroup.com.au / http://podiumtalentgroup.com.au/contact.php

4. Must Be Able to Coded for MOBILE-FRIENDLINESS & WordPress friendly Ideal.

5. This is the first, small job of many we/graphic design jobs. If suits, winning designer may be offered all future work direct.

Thanks & look forward to your design. Glen.

Target Market(s)

corporates - high end

Number of Pages Required

2 page

Font styles to use
Sans Serif

Requirements
Must have
• Classy professional look
Nice to have
• all in Video in brief
Should not have
• too many images / new images I haven't approved

```html
<!DOCTYPE html>
<html lang="en">
<head>
<meta charset="utf-8">
<title>Keynote Circle – Find The Perfect Speaker</title>
<link href="https://fonts.googleapis.com/css2?family=Roboto:wght@300;400;500;700&display=swap" rel="stylesheet">
<style>
  :root {
    --hero-dark: #3c4852;
    --hero-mid: #6d7a84;
    --hero-light: #a9b3ba;
    --white: #ffffff;
    --band-grey: #e4e7e9;
    --page-bg: #ffffff;
    --text: #4a5560;
    --heading: #5b6570;
    --rule: #c9ced2;
    --blue: #4fa3d9;
    --blue-band: #5badde;
    --green: #3fbf8c;
    --video-bg: #d9dcdc;
  }
  * { box-sizing: border-box; margin: 0; padding: 0; }
  html, body { width: 818px; height: 1200px; overflow: hidden; }
  body { font-family: "Roboto", Arial, sans-serif; background: var(--page-bg); color: var(--text); position: relative; }

  .hero {
    position: absolute; left: 0; top: 0; width: 818px; height: 330px;
    background: linear-gradient(160deg, var(--hero-mid) 0%, var(--hero-light) 45%, var(--hero-dark) 100%);
  }
  .hero__title { position: absolute; left: 34px; top: 20px; color: var(--white); font-size: 31px; font-weight: 400; letter-spacing: .2px; white-space: nowrap; }
  .hero__subtitle { position: absolute; left: 34px; top: 60px; color: var(--white); font-size: 24px; font-weight: 300; }
  .hero__rule { position: absolute; left: 34px; top: 102px; width: 750px; height: 1px; background: rgba(255,255,255,.55); }
  .hero__pitch { position: absolute; left: 308px; top: 200px; width: 490px; color: var(--white); font-size: 15px; line-height: 21px; font-weight: 300; white-space: nowrap; }
  .hero__pitch strong { font-weight: 700; }
  .hero__cta {
    position: absolute; left: 682px; top: 270px; width: 106px; height: 22px;
    border: 1px solid rgba(255,255,255,.8); color: var(--white);
    font-size: 9px; letter-spacing: 1px; display: flex; align-items: center; justify-content: center; gap: 6px;
  }

  .video-band { position: absolute; left: 0; top: 330px; width: 818px; height: 150px; background: var(--band-grey); }
  .video {
    position: absolute; left: 142px; top: 356px; width: 518px; height: 284px;
    background: linear-gradient(180deg, #cfd3d3 0%, var(--video-bg) 60%, #c8cccc 100%);
    box-shadow: 0 2px 6px rgba(0,0,0,.18);
  }
  .video__play { position: absolute; left: 238px; top: 110px; }
  .video__controls { position: absolute; left: 12px; bottom: 10px; width: 494px; height: 16px; }

  .success-btn {
    position: absolute; left: 265px; top: 671px; width: 295px; height: 28px;
    background: var(--blue); color: var(--white); font-size: 13px;
    display: flex; align-items: center; justify-content: center; gap: 8px;
  }

  .about { position: absolute; left: 34px; top: 755px; width: 750px; }
  .about__heading { display: flex; align-items: center; gap: 22px; font-size: 25px; font-weight: 300; color: var(--heading); justify-content: center; }
  .about__heading::before, .about__heading::after { content: ""; height: 1px; width: 120px; background: var(--rule); }
  .about__text { margin-top: 22px; font-size: 11.5px; line-height: 16px; }
  .about__text + .about__text { margin-top: 14px; }

  .enquiry {
    position: absolute; left: 0; top: 988px; width: 818px; height: 212px;
    background: var(--blue-band); color: var(--white); text-align: center;
  }
  .enquiry__list { list-style: none; padding-top: 40px; font-size: 11.5px; }
  .enquiry__list li { height: 33px; }
  .enquiry__btn {
    position: absolute; left: 295px; top: 184px; width: 228px; height: 22px;
    background: var(--green); color: var(--white); font-size: 10px; font-weight: 500; letter-spacing: .6px;
    display: flex; align-items: center; justify-content: center; gap: 6px;
  }
</style>
</head>
<body>

<header class="hero" role="img" aria-label="Photograph of an empty boardroom with a long conference table">
  <h1 class="hero__title">Find The Perfect Speaker For Your Next Event Here...</h1>
  <p class="hero__subtitle">free industrie service</p>
  <div class="hero__rule"></div>
  <p class="hero__pitch">Looking for a top motivational or guest speaker,<br>MC, industrie expert to <strong>"WOW"</strong> your next event? find them here</p>
  <div class="hero__cta">
    <svg width="8" height="8" viewBox="0 0 8 8"><path d="M1 4h6M4 1l3 3-3 3" stroke="#fff" fill="none"/></svg>
    CONTACT
  </div>
</header>

<div class="video-band"></div>

<section class="video" role="img" aria-label="Introduction video still of the speaker bureau founder">
  <svg class="video__play" width="42" height="48" viewBox="0 0 42 48"><path d="M0 0L42 24L0 48Z" fill="var(--green)"/></svg>
  <svg class="video__controls" viewBox="0 0 494 16">
    <circle cx="6" cy="8" r="5" fill="none" stroke="#7f8a8f"/>
    <circle cx="20" cy="8" r="5" fill="none" stroke="#7f8a8f"/>
    <circle cx="34" cy="8" r="5" fill="none" stroke="#7f8a8f"/>
    <rect x="46" y="7" width="430" height="2" fill="#aab2b5"/>
    <rect x="46" y="7" width="90" height="2" fill="var(--green)"/>
    <circle cx="486" cy="8" r="5" fill="none" stroke="var(--green)"/>
  </svg>
</section>

<div class="success-btn">
  I Want to Make our Event a Great Success
  <svg width="12" height="12" viewBox="0 0 12 12"><circle cx="6" cy="6" r="5" fill="none" stroke="#fff"/><path d="M4 6h4M6 4l2 2-2 2" stroke="#fff" fill="none"/></svg>
</div>

<section class="about">
  <h2 class="about__heading">About</h2>
  <p class="about__text">Keynote Circle is a free industry service designed to help people looking for speakers save precious time and frustration in finding the most suitable/best speaker for their needs.</p>
  <p class="about__text">Suggestions are given by Australian conference speaker Dean Calloway who has presented around Australia for a number of years and is familiar with many of our top professional speakers, MC's as well as the leading speaker bureaus.</p>
  <p class="about__text">If you would like a hand finding some good speaker options, simply send us the details of your event and the type of presenter you are ideally after, e.g.</p>
</section>

<section class="enquiry">
  <ul class="enquiry__list">
    <li>Type/Style – Motivational, Entertaining, Keynote/Workshop, MC etc</li>
    <li>Topic/Area – Team Building, Leadership, Inspiration, Health/Life Balance etc</li>
    <li>Approximate Budget – $1000, $3000, $5000, $7000+ etc</li>
    <li>Location – Sydney, Melbourne, Brisbane, Perth, Adelaide, Canberra etc</li>
  </ul>
  <div class="enquiry__btn">
    COMPLETE ONLINE CONTACT FORM
    <svg width="11" height="11" viewBox="0 0 12 12"><circle cx="6" cy="6" r="5" fill="none" stroke="#fff"/><path d="M4 6h4M6 4l2 2-2 2" stroke="#fff" fill="none"/></svg>
  </div>
</section>

</body>
</html>
```